Harbor Crest Holdings Corporate Showcase

Provide an attractive Corporate Website for a boutique Investment Company to showcase our activities and corporate interests.

Our Company works across a number of Sectors including

Real Estate
E-Commerce
Healthcare
Beauty & Personal Care
Technology
Resources

Lets keep the personality

Modern
Global
Sophisticated
Calm
Interesting

Lets keep the pages with MINIMAL Words
Lets use Photos/ Imagery to tell the story

We'll need a Banner Menu -
About Us
Expertise
Global Outlook
Sectors
Management
Media
Contact Us

Many thanks
Best wishes
Dennis.

Target Market(s)

Investors
Clients

Coding

Coded - Design and coding required

Number of Pages Required

5+ page

Font styles to use
Sans Serif

Colors
886aae
3176b5
00a990
f68e4d
f04a50
e667a6

Requirements
Must have
• WordPress Coding

Checkout this Website for look and feel - its cool:
www.qvr-example.com

Harbor Crest Partners
(Harbor Crest Holdings LLP)
London
E9 4ZX
United Kingdom

www.HarborCrestPartners-example.com
Nice to have
• Sophisticated colour palette - black/ brown/ blue/ purple/

```html
<!DOCTYPE html>
<html lang="en">
<head>
<meta charset="utf-8">
<title>Harbor Crest Holdings</title>
<link href="https://fonts.googleapis.com/css2?family=Outfit:wght@400;600;700&family=Raleway:wght@400;500;600;700&display=swap" rel="stylesheet">
<style>
:root{
  --purple:#886aae;
  --purple-dark:#7a5da0;
  --ink:#111111;
  --text:#444444;
  --muted:#8a8a8a;
  --grey-bg:#f4f4f4;
  --white:#ffffff;
  --black:#070707;
  --navy:#0b0f3a;
}
*{box-sizing:border-box;margin:0;padding:0}
html,body{width:1200px;height:4914px;overflow:hidden}
body{font-family:"Raleway",sans-serif;color:var(--text);background:var(--white)}
.page{position:relative;width:1200px;height:4914px;overflow:hidden}
.abs{position:absolute}
h1,h2,h3,.brand{font-family:"Outfit",sans-serif}

/* top bar */
.topbar{left:0;top:0;width:1200px;height:38px;background:var(--purple);color:#fff;font-size:15px;font-weight:600}
.topbar span{position:absolute;top:10px;display:flex;align-items:center;gap:8px}
/* nav */
.header{left:0;top:38px;width:1200px;height:84px;background:#fff}
.brand{position:absolute;left:90px;top:18px;color:var(--purple);font-weight:700;font-size:27px;line-height:1;letter-spacing:.5px}
.brand small{display:block;color:#333;font-size:15px;letter-spacing:5.5px;margin-top:6px;font-weight:600;padding-left:14px}
.nav{position:absolute;left:351px;top:34px;display:flex;gap:25px;font-size:15px;color:#333}
.nav .active{color:var(--purple);font-weight:700}

/* hero */
.hero{left:0;top:122px;width:1200px;height:593px;background:radial-gradient(ellipse at 18% 70%,#c44ab8 0%,#5a3bb0 18%,#1a1f6e 45%,var(--navy) 75%);text-align:center;color:#fff}
.hero h1{margin-top:245px;font-size:52px;font-weight:700;letter-spacing:2px;line-height:1}
.hero p{font-family:"Outfit",sans-serif;font-size:35px;font-weight:400;letter-spacing:1.5px;margin-top:6px}

.sec-title{font-size:44px;font-weight:700;color:var(--ink);line-height:1}
.bar{width:44px;height:5px;background:var(--purple);margin-top:16px}
.center{text-align:center}
.center .bar{margin-left:auto;margin-right:auto}
.copy{font-size:15.5px;line-height:27px;color:#333}
.btn{display:inline-block;background:var(--purple);color:#fff;font-weight:700;font-size:16px;border-radius:24px;text-align:center;line-height:48px;height:48px}

.purple-block{background:var(--purple)}
.photo{display:block}

/* sectors */
.sectors{left:0;top:1324px;width:1200px;height:1198px;background:var(--grey-bg)}
.card{background:#fff;width:330px;height:441px}
.card .photo{width:330px;height:234px}
.card .label{position:absolute;left:28px;top:208px;width:274px;height:51px;background:var(--purple);color:#fff;font-weight:700;font-size:16px;text-align:center;line-height:51px}
.card p{position:absolute;left:18px;right:18px;top:290px;text-align:center;font-size:14.5px;line-height:28px;color:#777}
.card .more{position:absolute;left:0;right:0;top:393px;text-align:center;color:var(--purple);font-weight:700;font-size:15px}

/* media */
.media-card{background:#fff;width:322px;height:481px;border:6px solid #e8e8e8;border-top:0}
.media-card.featured{border-color:var(--purple)}
.media-card .photo{width:100%;height:252px}
.avatar{position:absolute;right:10px;top:208px;width:86px;height:86px;border-radius:50%;border:4px solid #fff;background:linear-gradient(#c9a98e,#8d6a55)}
.media-card h3{position:absolute;left:20px;top:298px;font-size:21px;font-weight:700;color:var(--ink);line-height:24px}
.media-card p{position:absolute;left:20px;right:20px;top:360px;font-size:14.5px;line-height:28px;color:#777}
.media-card .more{position:absolute;right:20px;top:444px;color:var(--purple);font-weight:700;font-size:15px}
.meta{position:absolute;left:56px;top:152px;width:210px;height:100px;background:var(--purple);color:#fff;font-size:14px;text-align:center;line-height:28px;padding-top:18px}

/* contact */
.contact-band{left:0;top:4184px;width:1200px;height:730px;background:var(--black)}
.contact{left:90px;top:3883px;width:1020px;height:612px;background:var(--purple)}
.contact h2{color:#fff;text-align:center;margin-top:70px;font-size:44px;font-weight:700;line-height:1}
.contact .bar{background:#fff;margin:16px auto 0}
.field{position:absolute;background:#fff;font-size:14px;color:#999;padding:0 0 0 18px;display:flex;align-items:center;gap:6px}
.field.area{align-items:flex-start;padding-top:18px}
.submit{position:absolute;left:419px;top:494px;width:180px;height:46px;border:2px solid #fff;border-radius:24px;color:#fff;font-weight:700;font-size:16px;text-align:center;line-height:42px}

/* footer */
.footer{color:#fff}
.footer .brand{color:#fff}
.footer .brand small{color:#fff}
.f-title{font-family:"Outfit",sans-serif;font-weight:700;font-size:21px}
.f-dash{width:14px;height:2px;background:#fff;margin-top:18px}
.f-links{list-style:none;font-size:14px;line-height:30.5px}
.socials{display:flex;gap:24px}
.socials span{width:17px;height:17px;background:#fff;border-radius:3px;display:block}
.copyright{left:0;top:4866px;width:1200px;text-align:center;font-size:12px;color:#fff}
</style>
</head>
<body>
<div class="page">

  <div class="abs topbar">
    <span style="left:752px">
      <svg width="16" height="12" viewBox="0 0 16 12"><rect x="0.5" y="0.5" width="15" height="11" fill="#fff"/><path d="M1 1l7 6 7-6" stroke="#886aae" stroke-width="1.5" fill="none"/></svg>
      hello@harborcrest-example.com
    </span>
    <span style="left:970px">
      <svg width="14" height="14" viewBox="0 0 24 24"><path fill="#fff" d="M6.6 10.8a15 15 0 006.6 6.6l2.2-2.2a1 1 0 011-.25 11.4 11.4 0 003.6.6 1 1 0 011 1V20a1 1 0 01-1 1A17 17 0 013 4a1 1 0 011-1h3.5a1 1 0 011 1c0 1.25.2 2.45.6 3.6a1 1 0 01-.25 1z"/></svg>
      +8 000 000 000
    </span>
  </div>

  <header class="abs header">
    <div class="brand">HARBOR CREST<small>HOLDINGS</small></div>
    <nav class="nav">
      <span class="active">Home</span><span>About Us</span><span>Expertise</span><span>Global Outlook</span><span>Sectors</span><span>Management</span><span>Media</span><span>Contact Us</span>
    </nav>
  </header>

  <section class="abs hero" role="img" aria-label="Abstract wave of glowing purple and blue dots on a dark navy field">
    <h1>HARBOR CREST HOLDINGS</h1>
    <p>Growing the Next Generation of Business</p>
  </section>

  <!-- About -->
  <section class="about">
    <div class="abs purple-block" style="left:914px;top:715px;width:286px;height:609px"></div>
    <div class="abs photo" role="img" aria-label="Businessman looking over a city skyline at dusk with a world map overlay" style="left:626px;top:796px;width:574px;height:444px;background:linear-gradient(180deg,#7f95b8 0%,#a8b6cc 35%,#5b6d8f 60%,#2b3550 100%)"></div>
    <div class="abs" style="left:92px;top:848px;width:470px">
      <h2 class="sec-title">About Us</h2>
      <div class="bar"></div>
      <p class="copy" style="margin-top:30px">Lorem ipsum dolor sit amet, consectetur adipiscing elit, sed do eiusmod tempor incididunt ut labore et dolore magna aliqua. Ut enim ad minim veniam, quis nostrud exercitation</p>
      <p class="copy" style="margin-top:27px">Duis aute irure dolor in reprehenderit in voluptate velit esse cillum dolore eu fugiat nulla pariatur.</p>
      <span class="btn" style="margin-top:35px;width:182px">Read More</span>
    </div>
  </section>

  <!-- Sectors -->
  <section class="abs sectors">
    <div class="abs center" style="left:0;top:90px;width:1200px"><h2 class="sec-title">Sectors</h2><div class="bar"></div></div>

    <article class="abs card" style="left:90px;top:197px">
      <div class="photo" role="img" aria-label="Hands passing a small model house" style="background:linear-gradient(135deg,#2a3550,#9a7a60 55%,#e8e2da)"></div>
      <div class="label">Real Estate</div>
      <p>Lorem ipsum dolor sit met,onsectetur adipiscing elit, sed do eiusmod empor incididunt ut labore et dolore</p>
      <div class="more">Read More</div>
    </article>
    <article class="abs card" style="left:437px;top:197px">
      <div class="photo" role="img" aria-label="Online shopping on a laptop and phone" style="background:linear-gradient(135deg,#3a3a3a,#9aa0a8 50%,#d6d6d6)"></div>
      <div class="label">E-Commerce</div>
      <p>Lorem ipsum dolor sit met,onsectetur adipiscing elit, sed do eiusmod empor incididunt ut labore et dolore</p>
      <div class="more">Read More</div>
    </article>
    <article class="abs card" style="left:782px;top:197px">
      <div class="photo" role="img" aria-label="Doctor holding the hand of a senior patient" style="background:linear-gradient(135deg,#e6e6e4,#c9cfd2 50%,#9fa8ad)"></div>
      <div class="label">Healthcare</div>
      <p>Lorem ipsum dolor sit met,onsectetur adipiscing elit, sed do eiusmod empor incididunt ut labore et dolore</p>
      <div class="more">Read More</div>
    </article>

    <article class="abs card" style="left:90px;top:654px">
      <div class="photo" role="img" aria-label="Hand using a lotion pump bottle" style="background:linear-gradient(135deg,#dfe6ea,#f4f6f7 55%,#e9d8cd)"></div>
      <div class="label">Beauty &amp; Personal Care</div>
      <p>Lorem ipsum dolor sit met,onsectetur adipiscing elit, sed do eiusmod empor incididunt ut labore et dolore</p>
      <div class="more">Read More</div>
    </article>
    <article class="abs card" style="left:437px;top:654px">
      <div class="photo" role="img" aria-label="Team working around a desk with laptops and tablets" style="background:linear-gradient(135deg,#4a4a48,#8e8c86 50%,#c8c6c0)"></div>
      <div class="label">Technology</div>
      <p>Lorem ipsum dolor sit met,onsectetur adipiscing elit, sed do eiusmod empor incididunt ut labore et dolore</p>
      <div class="more">Read More</div>
    </article>
    <article class="abs card" style="left:782px;top:654px">
      <div class="photo" role="img" aria-label="Open pit mine lit at night" style="background:linear-gradient(160deg,#0d1a4a,#1d2f6a 55%,#3a4a7a)"></div>
      <div class="label">Resources</div>
      <p>Lorem ipsum dolor sit met,onsectetur adipiscing elit, sed do eiusmod empor incididunt ut labore et dolore</p>
      <div class="more">Read More</div>
    </article>
  </section>

  <!-- Global Outlook -->
  <section class="outlook">
    <div class="abs purple-block" style="left:0;top:2522px;width:315px;height:578px"></div>
    <div class="abs photo" role="img" aria-label="Financial chart lines over stacks of coins" style="left:0;top:2608px;width:590px;height:407px;background:linear-gradient(120deg,#c8a88a 0%,#8aa6bf 35%,#4f6f93 70%,#2b4466 100%)"></div>
    <div class="abs" style="left:628px;top:2618px;width:482px">
      <h2 class="sec-title">Global Outlook</h2>
      <div class="bar"></div>
      <p class="copy" style="margin-top:30px;text-align:justify;line-height:31.5px">Lorem ipsum dolor sit amet, consectetur adipiscing elit, sed do eiusmod tempor incididunt ut labore et dolore magna aliqua. Ut enim ad minim veniam, quis nostrud exercitation ullamco laboris nisi ut aliquip ex ea commodo consequat. Duis aute irure dolor in reprehenderit in voluptate velit esse cillum dolore eu fugiat nulla pariatur. Excepteur sint occaecat cupidatat non proident, sunt in culpa qui officia deserunt mollit anim id est laborum</p>
      <span class="btn" style="margin-top:30px;width:182px">Read More</span>
    </div>
  </section>

  <!-- Media -->
  <section class="media">
    <div class="abs" style="left:0;top:3100px;width:1200px;height:449px;background:var(--grey-bg)"></div>
    <div class="abs center" style="left:0;top:3196px;width:1200px"><h2 class="sec-title">Media</h2><div class="bar"></div></div>

    <article class="abs media-card" style="left:90px;top:3297px">
      <div class="photo" role="img" aria-label="Hourglass beside stacks of coins" style="background:linear-gradient(135deg,#eef0f2,#b9a27a 55%,#6b5a40)"></div>
      <div class="avatar" role="img" aria-label="Author portrait"></div>
      <h3>Lorem ipsum dolor<br>sit amet</h3>
      <p>Lorem ipsum dolor sit met,onsectetur adipiscing elit, sed do eiusmod empor incididunt ut labore et dolore</p>
      <div class="more">Read More</div>
    </article>
    <article class="abs media-card featured" style="left:439px;top:3297px">
      <div class="photo" role="img" aria-label="Digital target with technology icons" style="background:linear-gradient(135deg,#0a1a3a,#1f4a7a 55%,#0c2448)"></div>
      <div class="meta">Harbor Crest / By Admin<br>Jan25,2020</div>
      <div class="avatar" role="img" aria-label="Author portrait"></div>
      <h3>Lorem ipsum dolor<br>sit amet</h3>
      <p>Lorem ipsum dolor sit met,onsectetur adipiscing elit, sed do eiusmod empor incididunt ut labore et dolore</p>
      <div class="more">Read More</div>
    </article>
    <article class="abs media-card" style="left:794px;top:3297px">
      <div class="photo" role="img" aria-label="Person reviewing charts on a tablet at a desk" style="background:linear-gradient(135deg,#e6e9ee,#9aa8bb 50%,#2c3a55)"></div>
      <div class="avatar" role="img" aria-label="Author portrait"></div>
      <h3>Lorem ipsum dolor<br>sit amet</h3>
      <p>Lorem ipsum dolor sit met,onsectetur adipiscing elit, sed do eiusmod empor incididunt ut labore et dolore</p>
      <div class="more">Read More</div>
    </article>
  </section>

  <!-- Contact -->
  <div class="abs contact-band"></div>
  <section class="abs contact">
    <h2>Contact Us</h2>
    <div class="bar"></div>
    <div class="field" style="left:70px;top:158px;width:435px;height:54px">&#9786; First Name</div>
    <div class="field" style="left:517px;top:158px;width:416px;height:54px">&#9786; Last Name</div>
    <div class="field" style="left:70px;top:223px;width:863px;height:51px">&#9743; Your phone</div>
    <div class="field" style="left:70px;top:284px;width:863px;height:52px">&#9633; Your Email</div>
    <div class="field area" style="left:70px;top:347px;width:863px;height:134px">&#9675; How Can we help you?</div>
    <div class="submit">Submit</div>
  </section>

  <!-- Footer -->
  <footer class="footer">
    <div class="brand" style="top:4570px">HARBOR CREST<small>HOLDINGS</small></div>
    <div class="abs socials" style="left:90px;top:4661px"><span></span><span></span><span></span><span></span><span></span></div>

    <div class="abs" style="left:450px;top:4576px">
      <div class="f-title">Links</div><div class="f-dash"></div>
    </div>
    <ul class="abs f-links" style="left:450px;top:4642px">
      <li>Home</li><li>About Us</li><li>Expertise</li><li>Global Outlook</li>
    </ul>
    <ul class="abs f-links" style="left:721px;top:4642px">
      <li>Sectors</li><li>Management</li><li>Media</li><li>Contact Us</li>
    </ul>
    <div class="abs" style="left:1005px;top:4576px">
      <div class="f-title">Important</div><div class="f-dash"></div>
    </div>
    <ul class="abs f-links" style="left:1006px;top:4642px">
      <li>Sign In</li><li>FAQ</li><li>Career</li>
    </ul>
    <div class="abs copyright">Copyright © 2021 | Harbor Crest Holdings | All rights reserved.</div>
  </footer>

</div>
</body>
</html>
```